KTR Photography Editing & Support Services for Real Estate

We require a double sided A4 flyer to promote our photography services to real estate agencies.
This particular service is targeted to rural areas where reliable, professional and highly skilled photographers are difficult to source. We teach the agent how to photograph, they upload files to a server and we take care of the rest (image editing, quality control and delivery). This will give the agents flexibility with when to shoot and eliminates the stress of managing a photographer / contractor. We offer a 1 day face to face training session and competitive packages for equipment start up.
We would like the flyer to look clean & very professional. The flyer should showcase samples of our work to highlight what can be achieved by using our services. We like the look of a black or dark background behind the text and feel that would look nice with our photographs provided. Otherwise open to your suggestions and ideas.
TEXT FOR FLYER:
Welcome to the KTR Real Estate Photography Editing and Support Service
• Take your real estate business to the next level by providing impressive real estate imagery that makes you stands out from the competition
• Omit the stress of trying to find a good photographer or managing an unreliable one and hence have more time to focus on other aspects of your business
• Showcase your listings with better quality and more impactful photographs than your competitors thereby increasing potential for a quick sale
• Great first impressions matter and you will achieve this by looking and feeling more professional. This will attract and retain more future clients.
HOW IT WORKS
• We understand that your time is valuable, so let us handle the editing and delivery of your images. You shoot, and we take care of the rest.
• Images are edited and delivered within 1 working day
INCLUSIONS:
• Full day face to face training (we come to you) and instructional handbook
• We will teach you everything you need to know about your equipment and how to take stunning real estate photographs
• Service turnaround within 1 working day
• Free HELP desk service Mon-Fri
• 12 month Exclusivity (rural towns only) for a limited time
INVESTMENT
• 99 per listing for us to manage images including editing, quality control and delivery (10 Images)
• Ask us about competitive packages for photography equipment if required
SUMMARY
The KTR Real Estate Photography Editing and Support Service is the perfect solution for busy real estate professionals who want to take their business to the next level. Our service is affordable, flexible, and designed to help you showcase your listings in the best possible light.
Contact us today to learn more about how we can help you.

```html
<!DOCTYPE html>
<html lang="en">
<head>
<meta charset="utf-8">
<title>KTR Real Estate Photography Flyer</title>
<link href="https://fonts.googleapis.com/css2?family=Montserrat:wght@300;400;500;600;700&display=swap" rel="stylesheet">
<style>
:root{
  --ink:#333335;
  --band:#c7c7c7;
  --mid:#8d8d8d;
  --paper:#ffffff;
  --stage:#bdbdbd;
  --pill:#7a7a7a;
  --rule:#9a9a9a;
}
*{box-sizing:border-box;margin:0;padding:0}
html,body{width:896px;height:1200px;overflow:hidden}
body{background:var(--stage);font-family:'Montserrat',sans-serif;color:var(--ink);position:relative}
.page{position:absolute;top:303px;width:420px;height:594px;background:var(--paper);overflow:hidden;box-shadow:0 6px 18px rgba(0,0,0,.28)}
.page--front{left:20px}
.page--back{left:456px;background:var(--ink)}
.layer{position:absolute;left:0;top:0}
.brand{position:absolute;left:133px;top:0;width:161px;height:63px;background:rgba(110,114,124,.5);border-radius:0 0 14px 14px;color:#fff;font-weight:300;text-align:center;padding-top:17px}
.brand__name{font-size:13px;letter-spacing:2.4px;display:block}
.brand__role{font-size:8px;letter-spacing:2.2px;display:block;margin-top:2px}
.welcome{position:absolute;left:112px;width:200px;top:282px;text-align:center;color:#fff;line-height:1.25}
.welcome__small{font-size:10px;font-weight:500}
.welcome__big{font-size:12.5px;font-weight:700}
.welcome__big span{font-size:9.5px;font-weight:500}
.welcome__sub{font-size:9.5px;font-weight:600}
.tab{position:absolute;left:50%;transform:translateX(-50%);font-size:9.5px;font-weight:700;letter-spacing:.3px;padding:2px 9px;border-radius:0 0 6px 6px;white-space:nowrap}
.tab--light{background:var(--paper);color:var(--ink)}
.tab--dark{background:var(--ink);color:#fff}
.services{position:absolute;left:0;top:359px;width:420px;height:123px;background:var(--band);border-top:3px solid var(--mid)}
.works{position:absolute;left:0;top:482px;width:420px;height:82px;background:var(--paper);border-top:3px solid var(--ink)}
.point{position:absolute;font-size:6.7px;letter-spacing:-.1px;line-height:9.4px;color:var(--ink);padding-left:9px;white-space:nowrap}
.point::before{content:"";position:absolute;left:0;top:3px;width:4px;height:4px;border-radius:50%;background:var(--ink)}
.rule-v{position:absolute;width:1px;background:var(--rule)}
.footer{position:absolute;left:0;bottom:0;width:420px;height:31px;background:var(--ink);color:#fff}
.footer svg.slant{position:absolute;left:0;top:0}
.footer__phone{position:absolute;left:24px;top:8px;display:flex;align-items:center;gap:7px;font-size:10px;font-weight:700}
.footer__follow{position:absolute;left:129px;top:7px;height:17px;border-left:1px solid var(--rule);padding-left:10px;display:flex;align-items:center;gap:6px;font-size:6px}
.footer__dot{width:11px;height:11px;border-radius:50%;background:#fff}
.footer__mail{position:absolute;left:262px;top:10px;display:flex;align-items:center;gap:6px;font-size:7.4px;font-weight:700;color:var(--ink)}
.incl{position:absolute;left:0;top:42px;width:420px;list-style:none;text-align:center;color:#fff;font-size:9px;line-height:11.2px}
.incl li{margin-bottom:7.5px}
.incl li::before{content:"\2022  ";}
.logo-centre{position:absolute;left:131px;top:238px;width:160px;text-align:center;color:#fff;font-weight:300}
.logo-centre .brand__name{font-size:12px;letter-spacing:2.2px}
.logo-centre .brand__role{font-size:7.5px}
.point--light{color:#fff}
.point--light::before{background:#fff}
.rule-h{position:absolute;left:0;width:420px;height:2px;background:var(--rule)}
.summary{position:absolute;left:10px;width:400px;top:480px;text-align:center;color:#fff;font-size:6.7px;letter-spacing:-.05px;line-height:9.6px;white-space:nowrap}
.cta{position:absolute;left:0;top:523px;width:420px;height:35px;background:var(--paper)}
.cta__pill{position:absolute;left:84px;top:8px;width:250px;height:16px;border-radius:4px;background:var(--pill);color:#fff;font-size:7.2px;text-align:center;line-height:16px;white-space:nowrap}
.footer--back{height:36px}
</style>
</head>
<body>

<section class="page page--front">
  <svg class="layer" width="420" height="359" viewBox="0 0 420 359">
    <defs>
      <linearGradient id="heroTone" x1="0" y1="0" x2="1" y2="1">
        <stop offset="0" stop-color="#5d6571"/><stop offset=".5" stop-color="#2f3540"/><stop offset="1" stop-color="#4a4f58"/>
      </linearGradient>
    </defs>
    <rect x="0" y="0" width="420" height="359" fill="url(#heroTone)" role="img" aria-label="Photo of a modern living room with a dark sofa, cushions and sheer curtains"/>
    <polygon points="0,214 212,330 420,208 420,359 0,359" fill="#ffffff"/>
    <polygon points="0,359 0,335 212,252 420,330 420,359" fill="#333335"/>
    <g class="frame-mid">
      <polygon points="212,120 267,175 212,230 157,175" fill="#fff"/>
      <polygon points="212,125 262,175 212,225 162,175" fill="#7a7a7a"/>
      <polygon points="212,130 257,175 212,220 167,175" fill="#d6cbbd" role="img" aria-label="Photo of a bathroom with arched mirrors and twin basins"/>
    </g>
    <g class="frame-left">
      <polygon points="101,132 199,230 101,328 3,230" fill="#fff"/>
      <polygon points="101,138 193,230 101,322 9,230" fill="#7a7a7a"/>
      <polygon points="101,144 187,230 101,316 15,230" fill="#cfc6ba" role="img" aria-label="Photo of a bright kitchen and dining area with timber beams"/>
    </g>
    <g class="frame-right">
      <polygon points="319,132 419,232 319,332 219,232" fill="#fff"/>
      <polygon points="319,138 413,232 319,326 225,232" fill="#7a7a7a"/>
      <polygon points="319,144 407,232 319,320 231,232" fill="#a7aec0" role="img" aria-label="Photo of a white farmhouse exterior at dusk"/>
    </g>
  </svg>

  <div class="brand"><span class="brand__name">KAI TORRENS</span><span class="brand__role">PHOTOGRAPHER</span></div>

  <div class="welcome">
    <div class="welcome__small">Welcome to</div>
    <div class="welcome__big"><span>the</span> KTR Real Estate</div>
    <div class="welcome__big">Photography Editing</div>
    <div class="welcome__sub">and Support Service</div>
  </div>

  <div class="services">
    <div class="tab tab--light" style="top:5px">OUR SERVICES</div>
    <p class="point" style="left:20px;top:28px">Take your real estate business to the next<br>level by providing impressive real estate<br>imagery that makes you stands out<br>from the competition.</p>
    <p class="point" style="left:20px;top:75px">Omit the stress of trying to find a good<br>photographer or managing an unreliable<br>one and hence have more time to focus<br>on other aspects of your business.</p>
    <div class="rule-v" style="left:206px;top:35px;height:70px"></div>
    <p class="point" style="left:222px;top:28px">Great first impressions matter and you will<br>achieve this by looking and feeling more<br>professional. This will attract and retain<br>more future clients.</p>
    <p class="point" style="left:222px;top:73px">Showcase your listings with better quality and<br>more impactful photographs than your<br>competitors thereby increasing potential for<br>a quick sale.</p>
  </div>

  <div class="works">
    <div class="tab tab--dark" style="top:1px">HOW IT WORKS</div>
    <p class="point" style="left:20px;top:26px">We understand that your time is valuable,<br>so let us handle the editing and delivery<br>of your images. You shoot, and we take<br>care of the rest.</p>
    <div class="rule-v" style="left:203px;top:22px;height:44px"></div>
    <p class="point" style="left:222px;top:36px">Images are edited and delivered within<br>1 working day</p>
  </div>

  <footer class="footer">
    <svg class="slant" width="420" height="31" viewBox="0 0 420 31">
      <polygon points="200,31 250,0 272,0 222,31" fill="#8d8d8d"/>
      <polygon points="222,31 272,0 420,0 420,31" fill="#c7c7c7"/>
    </svg>
    <div class="footer__phone">
      <svg width="12" height="12" viewBox="0 0 16 16"><circle cx="8" cy="8" r="7.2" fill="none" stroke="#fff" stroke-width="1.2"/><path d="M5 4h2l.7 2-1.2 1a5 5 0 0 0 2.5 2.5l1-1.2 2 .7v2a1 1 0 0 1-1 1A7 7 0 0 1 4 5a1 1 0 0 1 1-1z" fill="#fff"/></svg>
      <span>61 400 555 018</span>
    </div>
    <div class="footer__follow"><span>Follow us:</span><span class="footer__dot"></span></div>
    <div class="footer__mail">
      <svg width="11" height="8" viewBox="0 0 11 8"><rect x=".5" y=".5" width="10" height="7" fill="none" stroke="#333335"/><path d="M.5 .5l5 4 5-4" fill="none" stroke="#333335"/></svg>
      <span>shoot@kaitorrens.com.au</span>
    </div>
  </footer>
</section>

<section class="page page--back">
  <svg class="layer" width="420" height="378" viewBox="0 0 420 378">
    <rect x="0" y="105" width="420" height="273" fill="#e3e1dd" role="img" aria-label="Faint photo of a bright white interior"/>
    <rect x="0" y="0" width="420" height="170" fill="#3a3a3c" role="img" aria-label="Faint dark interior photo behind the inclusions"/>
    <polygon points="0,128 211,178 420,128 420,180 0,180" fill="#e3e1dd"/>
    <polygon points="100,378 211,318 322,378" fill="#333335"/>
    <g class="frame-left">
      <polygon points="69,170 157,258 69,346 -19,258" fill="#fff"/>
      <polygon points="69,175 152,258 69,341 -14,258" fill="#333335"/>
      <polygon points="69,178 149,258 69,338 -11,258" fill="#2f3a52" role="img" aria-label="Photo of a glass-walled living room at night with mountain views"/>
    </g>
    <g class="frame-right">
      <polygon points="348,173 436,261 348,349 260,261" fill="#fff"/>
      <polygon points="348,178 431,261 348,344 265,261" fill="#333335"/>
      <polygon points="348,181 428,261 348,341 268,261" fill="#9b7d5e" role="img" aria-label="Photo of a hallway bench with framed pictures and woven baskets"/>
    </g>
    <g class="frame-centre">
      <polygon points="211,165 301,255 211,345 121,255" fill="#fff"/>
      <polygon points="211,170 296,255 211,340 126,255" fill="#333335"/>
      <polygon points="211,175 291,255 211,335 131,255" fill="#3d3e41" role="img" aria-label="Photo of a dark timber house exterior at dusk"/>
    </g>
  </svg>

  <div class="tab tab--light" style="top:16px;border-radius:6px;padding:3px 12px">INCLUSIONS</div>
  <ul class="incl">
    <li>Full day face to face training (we come to you) and instructional handbook</li>
    <li>We will teach you everything you need to know about your equipment and<br>how to take stunning real estate photographs</li>
    <li>Service turnaround within 1 working day</li>
    <li>Free HELP desk service Mon-Fri</li>
    <li>12 month Exclusivity (rural towns only) for a limited time</li>
  </ul>

  <div class="logo-centre"><span class="brand__name">KAI TORRENS</span><span class="brand__role">PHOTOGRAPHER</span></div>

  <div class="tab tab--light" style="top:360px;border-radius:6px;padding:3px 12px">INVESTMENT</div>
  <p class="point point--light" style="left:30px;top:404px">99 per listing for us to manage images<br>including editing, quality control and<br>delivery (10 Images)</p>
  <div class="rule-v" style="left:207px;top:400px;height:40px"></div>
  <p class="point point--light" style="left:229px;top:404px">Ask us about competitive packages for<br>photography equipment if required</p>

  <div class="rule-h" style="top:455px"></div>
  <div class="tab tab--light" style="top:456px;border-radius:0 0 6px 6px;padding:3px 12px">SUMMARY</div>
  <p class="summary">The KTR Real Estate Photography Editing and Support Service is the perfect solution for busy real<br>estate professionals who want to take their business to the next level. Our service is affordable,<br>flexible, and designed to help you showcase your listings in the best possible light.</p>

  <div class="cta"><div class="cta__pill">Contact us today to learn more about how we can help you.</div></div>

  <footer class="footer footer--back">
    <svg class="slant" width="420" height="36" viewBox="0 0 420 36">
      <polygon points="200,36 250,0 272,0 222,36" fill="#8d8d8d"/>
      <polygon points="222,36 272,0 420,0 420,36" fill="#c7c7c7"/>
    </svg>
    <div class="footer__phone" style="top:11px">
      <svg width="12" height="12" viewBox="0 0 16 16"><circle cx="8" cy="8" r="7.2" fill="none" stroke="#fff" stroke-width="1.2"/><path d="M5 4h2l.7 2-1.2 1a5 5 0 0 0 2.5 2.5l1-1.2 2 .7v2a1 1 0 0 1-1 1A7 7 0 0 1 4 5a1 1 0 0 1 1-1z" fill="#fff"/></svg>
      <span>61 400 555 018</span>
    </div>
    <div class="footer__follow" style="top:10px"><span>Follow us:</span><span class="footer__dot"></span></div>
    <div class="footer__mail" style="top:13px">
      <svg width="11" height="8" viewBox="0 0 11 8"><rect x=".5" y=".5" width="10" height="7" fill="none" stroke="#333335"/><path d="M.5 .5l5 4 5-4" fill="none" stroke="#333335"/></svg>
      <span>shoot@kaitorrens.com.au</span>
    </div>
  </footer>
</section>

</body>
</html>
```